Web design for sitter site

We will be launching a sitter site in the coming months that focuses on sitters for children. The name of this site will be NestWatch.com
We will need:
1. main page design
2. site logo designed
3. subpages as well for the look of people's profiles, and job listings, etc (see links below)
We only need the design, photos, font files, etc. We do not need this site coded (no html), a ps job is fine.
Some competing sites in the space include - tendlane.com and brio.com
http://www.pebble-keeper.example/images/profile1.jpg
http://marrowbooks.example/wp-content/uploads/2013/09/brio-review.png
http://www.quillmont.example/hr/photos/tend_lane2.jpg
Thanks for your interest!
Mothers of children, mainly women
Online

```html
<!DOCTYPE html>
<html lang="en">
<head>
<meta charset="utf-8">
<title>NestWatch</title>
<link href="https://fonts.googleapis.com/css2?family=Open+Sans:ital,wght@0,300;0,400;0,600;0,700;1,400&display=swap" rel="stylesheet">
<style>
:root{
  --cyan:#16d4e8;
  --cyan-dark:#35b3c2;
  --orange:#f4581a;
  --teal:#52b1a3;
  --teal-btn:#3d9c92;
  --green:#3fa51b;
  --ink:#333;
  --muted:#555;
  --footer:#363636;
  --footer-bottom:#2b2b2b;
  --link:#2ec7d8;
}
*{box-sizing:border-box;margin:0;padding:0}
html,body{width:678px;height:1200px;overflow:hidden}
body{position:relative;font-family:"Open Sans",Arial,sans-serif;color:var(--ink);background:#fff}
.abs{position:absolute}
.topbar{left:0;top:0;width:678px;height:62px;background:var(--cyan);border-top:2px solid #3fb3b8}
.account{left:542px;top:0;width:92px;height:18px;background:var(--cyan-dark);color:#fff;font-size:7px;font-weight:600;text-align:center;line-height:18px;clip-path:polygon(0 0,100% 0,94% 100%,6% 100%)}
.brand{left:42px;top:30px;display:flex;align-items:center;gap:8px;color:#fff;font-size:20px;font-weight:400}
.brand-dot{width:22px;height:22px;border-radius:50%;background:#fff}
.nav{left:258px;top:37px;display:flex;font-size:7.2px;color:#1d3b44;align-items:center}
.nav span{padding:0 7px;line-height:17px}
.nav .active{background:var(--orange);color:#fff;padding:0 11px;font-weight:600}
.hero-band{left:0;top:62px;width:678px;height:282px;background:linear-gradient(100deg,#d8f0d6 0%,#bfe7de 40%,#6cc3b9 100%)}
.hero{left:42px;top:69px;width:595px;height:225px;border:3px solid #fff;background:linear-gradient(90deg,#eeeeee 0%,#e6e6e6 45%,#d9dcd6 60%,#c9cfc8 100%)}
.hero-title{left:66px;top:103px;width:300px;font-size:24px;font-weight:300;line-height:27px;color:var(--orange)}
.hero-copy{left:67px;top:163px;width:250px;font-size:7.8px;line-height:12px;color:#333}
.btn-start{left:66px;top:209px;width:98px;height:25px;background:#1cc9e0;border:1px solid #11a9bd;color:#fff;font-size:7.5px;font-weight:600;text-align:center;line-height:23px;letter-spacing:.3px}
.dots{display:flex;gap:4px}
.dots i{width:8px;height:8px;border-radius:50%;background:#888;display:block}
.hero-dots{left:66px;top:271px}
.hero-dots i:first-child{background:var(--orange)}
.options{left:42px;top:302px;width:596px;height:115px;background:#fff;box-shadow:0 1px 4px rgba(0,0,0,.2)}
.options h2{position:absolute;left:0;right:0;top:9px;text-align:center;font-size:12.5px;font-weight:400}
.option{top:36px;width:274px;height:73px;border:1px solid #999;text-align:center}
.option h3{margin-top:9px;font-size:10.5px;font-weight:400;color:var(--orange);letter-spacing:.3px}
.option p{font-size:7.5px;margin-top:2px}
.option .btn-go{display:inline-block;margin-top:8px;width:93px;height:19px;line-height:19px;background:var(--green);color:#fff;font-size:7.8px;font-weight:600}
.section-title{left:0;width:678px;text-align:center;font-size:13.5px;font-weight:400}
.section-lead{left:100px;width:478px;text-align:center;font-size:6.8px;line-height:12px;color:var(--muted)}
.offer{top:496px;width:186px;height:191px;background:#f2f2f2}
.offer .photo{margin:8px 9px 0;height:85px}
.offer h3{margin:13px 9px 0;font-size:10.5px;font-weight:400;color:var(--orange);letter-spacing:.3px}
.offer p{margin:2px 9px 0;font-size:6.8px;line-height:12px;color:var(--muted)}
.offer .btn-more{display:block;margin:8px 9px 0;width:63px;height:18px;line-height:18px;background:var(--teal-btn);color:#fff;font-size:6.8px;font-weight:600;text-align:center}
.how-band{left:0;top:702px;width:678px;height:206px;background:var(--teal)}
.how-band .section-title,.how-band .section-lead{color:#fff}
.step{top:81px;width:186px;height:89px;border:2px solid #7ecbbf;background:linear-gradient(#fff,#e3e3e3)}
.step svg{position:absolute;left:9px;top:12px}
.step h3{position:absolute;left:33px;top:8px;font-size:10.5px;font-weight:600;color:var(--orange);letter-spacing:.2px}
.step p{position:absolute;left:33px;top:24px;width:145px;font-size:6.8px;line-height:12px;color:var(--muted)}
.quote-mark{font-size:22px;color:var(--teal);font-weight:700;line-height:1}
.quote-text{left:60px;top:954px;width:558px;text-align:center;font-size:6.8px;line-height:12px;font-style:italic;color:var(--muted)}
.quote-name{left:0;width:678px;top:999px;text-align:center;font-size:7px;color:var(--orange);font-weight:600}
.quote-place{left:0;width:678px;top:1010px;text-align:center;font-size:6.6px;color:var(--teal);font-style:italic}
.quote-dots{left:323px;top:1043px}
.quote-dots i{width:7px;height:7px}
.quote-dots i:first-child{background:#222}
.footer{left:0;top:1070px;width:678px;height:100px;background:var(--footer)}
.footer-col{top:1085px;font-size:6.5px;color:#ccc;line-height:13px}
.footer-col h4{font-size:8px;font-weight:400;color:var(--link);margin-bottom:3px}
.footer-bottom{left:0;top:1170px;width:678px;height:30px;background:var(--footer-bottom)}
.copyright{left:42px;top:1181px;font-size:6.4px;color:#aaa}
.copyright b{font-weight:400;color:var(--link)}
.social{left:576px;top:1178px;display:flex;gap:4px}
.social i{display:block;width:13px;height:13px}
</style>
</head>
<body>

<div class="abs topbar"></div>
<div class="abs account">Sign in &nbsp;|&nbsp; Join Now</div>
<div class="abs brand"><span class="brand-dot"></span>NestWatch</div>
<nav class="abs nav">
  <span class="active">Home</span><span>About Us</span><span>Child Care</span><span>Senior Care</span><span>Pet Care</span><span>How it Works</span><span>What We Offers</span><span>Contact</span>
</nav>

<div class="abs hero-band"></div>
<div class="abs hero" role="img" aria-label="Smiling grandmother holding a laughing baby at a home office desk"></div>
<h1 class="abs hero-title">Pellentesque habitant morbi tristique</h1>
<p class="abs hero-copy">Aenean a nibh eget turpis vehicula tempus ac sed massa. Vestibulum dolor nulla, ultrices ac tincidunt sed, laoreet non est dignissim lectus vitae eros placerat euismod..</p>
<div class="abs btn-start">GET STARTED NOW</div>
<div class="abs dots hero-dots"><i></i><i></i><i></i><i></i></div>

<section class="abs options">
  <h2>Let’s Get Started. Choose an Options</h2>
  <div class="abs option" style="left:16px">
    <h3>I need a CareGiver</h3>
    <p>Start your free search for care in your area.</p>
    <span class="btn-go">Find Care Now</span>
  </div>
  <div class="abs option" style="left:305px">
    <h3>I want a CareJob</h3>
    <p>Create a free profile and search for jobs.</p>
    <span class="btn-go">Find Jobs Now</span>
  </div>
</section>

<h2 class="abs section-title" style="top:436px">What We Offers</h2>
<p class="abs section-lead" style="top:459px">Aliquam molestie, mi et imperdiet euismod, dui purus auctor tellus, et interdum lacus lectus et ante. Sed accumsan sollicitudin sapien, sit amet adipiscing turpis gravida ac.</p>

<article class="abs offer" style="left:42px">
  <div class="photo" role="img" aria-label="Mother painting with two young children" style="background:linear-gradient(90deg,#d9442e,#e9b46a 50%,#5fb5d8)"></div>
  <h3>Child Care</h3>
  <p>Aliquam molestie, mi et imperdiet euismod, dui purus auctor tellus, et interdum lacus lectus et ante. Sed accumsan sollicitudin sapien..</p>
  <span class="btn-more">READ MORE</span>
</article>
<article class="abs offer" style="left:246px">
  <div class="photo" role="img" aria-label="Caregiver with an elderly couple at home" style="background:linear-gradient(90deg,#c9c2b2,#a7a49a 50%,#d7d1c3)"></div>
  <h3>Senior Care</h3>
  <p>Aliquam molestie, mi et imperdiet euismod, dui purus auctor tellus, et interdum lacus lectus et ante. Sed accumsan sollicitudin sapien..</p>
  <span class="btn-more">READ MORE</span>
</article>
<article class="abs offer" style="left:450px">
  <div class="photo" role="img" aria-label="Man hugging his dog on a lawn" style="background:linear-gradient(90deg,#b07b5f,#5b6b3b 55%,#7e9a4a)"></div>
  <h3>Pet Care</h3>
  <p>Aliquam molestie, mi et imperdiet euismod, dui purus auctor tellus, et interdum lacus lectus et ante. Sed accumsan sollicitudin sapien..</p>
  <span class="btn-more">READ MORE</span>
</article>

<section class="abs how-band">
  <h2 class="abs section-title" style="top:22px">How it Works</h2>
  <p class="abs section-lead" style="top:44px">Aliquam molestie, mi et imperdiet euismod, dui purus auctor tellus, et interdum lacus lectus et ante. Sed accumsan sollicitudin sapien, sit amet adipiscing turpis gravida ac.</p>
  <div class="abs step" style="left:42px">
    <svg width="18" height="20" viewBox="0 0 18 20" fill="#666"><circle cx="5" cy="3" r="2.5"/><rect x="2.5" y="6" width="5" height="8"/><rect x="3" y="13" width="1.8" height="7"/><rect x="5.2" y="13" width="1.8" height="7"/><circle cx="12.5" cy="9" r="2"/><rect x="10.5" y="11.5" width="4" height="5"/><rect x="11" y="16" width="1.4" height="4"/><rect x="12.7" y="16" width="1.4" height="4"/></svg>
    <h3>Parents: Post Your Job</h3>
    <p>Aliquam molestie, mi et imperdiet euismod, dui purus auctor tellus, et interdum lacus lectus et ante. Sed accumsan sollicitudin sapien..</p>
  </div>
  <div class="abs step" style="left:246px">
    <svg width="20" height="18" viewBox="0 0 20 18" fill="#666"><circle cx="10" cy="5" r="4"/><path d="M1 18c0-6 4-8 9-8s9 2 9 8z"/></svg>
    <h3>Caregivers: Apply to Jobs</h3>
    <p>Aliquam molestie, mi et imperdiet euismod, dui purus auctor tellus, et interdum lacus lectus et ante. Sed accumsan sollicitudin sapien..</p>
  </div>
  <div class="abs step" style="left:450px">
    <svg width="20" height="18" viewBox="0 0 20 18" fill="#666"><path d="M1 9l3-3 4 5L17 1l2 2L8 17z"/></svg>
    <h3>Find the Right Match</h3>
    <p>Aliquam molestie, mi et imperdiet euismod, dui purus auctor tellus, et interdum lacus lectus et ante. Sed accumsan sollicitudin sapien..</p>
  </div>
</section>

<h2 class="abs section-title" style="top:924px">What Other Says...</h2>
<span class="abs quote-mark" style="left:41px;top:953px">“</span>
<span class="abs quote-mark" style="left:626px;top:953px">”</span>
<p class="abs quote-text">Aliquam molestie, mi et imperdiet euismod, dui purus auctor tellus, et interdum lacus lectus et ante. Sed accumsan sollicitudin sapien, sit amet adipiscing turpis gravida ac. In congue, neque ac lobortis volutpat, libero mauris varius mi, vitae suscipit ipsum ligula vitae risus. Duis aliquam nibh a dui iaculis viverra id a velit. Vivamus egestas risus in magna varius commodo. Sed semper viverra egestas. Etiam pretium porttitor lectus, vel ornare neque porta volutpat.</p>
<p class="abs quote-name">Name goes her</p>
<p class="abs quote-place">Location</p>
<div class="abs dots quote-dots"><i></i><i></i><i></i></div>

<footer>
  <div class="abs footer"></div>
  <div class="abs footer-col" style="left:42px"><h4>Footer Links</h4>Vivamus egestas<br>Risus in magna<br>Varius commodo<br>Sed semper<br>Vehicula tempus ac</div>
  <div class="abs footer-col" style="left:149px"><h4>Footer Links</h4>Vivamus egestas<br>Risus in magna<br>Varius commodo<br>Sed semper<br>Vehicula tempus ac</div>
  <div class="abs footer-col" style="left:257px"><h4>Footer Links</h4>Vivamus egestas<br>Risus in magna<br>Varius commodo<br>Sed semper<br>Vehicula tempus ac</div>
  <div class="abs footer-col" style="left:364px"><h4>Footer Links</h4>Vivamus egestas<br>Risus in magna<br>Varius commodo<br>Sed semper<br>Vehicula tempus ac</div>
  <div class="abs footer-col" style="left:471px"><h4>Footer Links</h4>Vivamus egestas<br>Risus in magna<br>Varius commodo<br>Sed semper<br>Vehicula tempus ac</div>
  <div class="abs footer-col" style="left:578px"><h4>Footer Links</h4>Vivamus egestas<br>Risus in magna<br>Varius commodo<br>Sed semper<br>Vehicula tempus ac</div>
  <div class="abs footer-bottom"></div>
  <p class="abs copyright">Copyright © 2014. <b>NestWatch</b>. All Right Reserved</p>
  <div class="abs social">
    <i style="background:#3b5998"></i><i style="background:#2aa9e0"></i><i style="background:#d73d32"></i><i style="background:#c4302b"></i>
  </div>
</footer>

</body>
</html>
```